Business Card Design Project

This is the first time we use our new logo. We need a business card that we can use both on our institutional corporate relationships and also that works for our staff that deals with consumers directly.

VELUNDA is a new company dedicated to empower consumers and to provide them with the best choices for specialized health care using the latest telemedicine technology (medicine at a distance via videoconference).

We want to print this cards in high quality materials and process. We will like designs that allow us to use UV spot varnish and other techniques that will differentiate us.

We are including Two different versions of Color logos. In addition we are including white over black background logos. Those can be used replacing the black for a color.

Please note this is the first time we will be creating any corporate materials with our new logo and colors.

Target Market(s)

34+ consumers of medium high and high socioeconomic levels.

Industry/Entity Type

Health

Requirements
Must have
• Our logo on its original colors
Should not have
• Any other graphical element or design that is not our logo

```html
<!DOCTYPE html>
<html lang="en">
<head>
<meta charset="utf-8">
<title>Velunda Business Card</title>
<link href="https://fonts.googleapis.com/css2?family=Arimo:wght@400;700&family=Jost:wght@600&display=swap" rel="stylesheet">
<style>
  :root {
    --navy: #1b5580;
    --sky: #5ab4de;
    --teal: #1fa895;
    --ink: #222222;
    --paper: #ffffff;
    --divider: #cfcfcf;
    --backdrop: #e9e9ef;
  }
  * { box-sizing: border-box; margin: 0; padding: 0; }
  html, body { width: 1200px; height: 987px; overflow: hidden; }
  body {
    background: var(--backdrop);
    position: relative;
    font-family: "Arimo", Arial, sans-serif;
  }
  .card {
    position: absolute;
    width: 600px;
    height: 340px;
    border-radius: 22px;
    overflow: hidden;
    box-shadow: 0 14px 30px rgba(0,0,0,0.18);
  }
  /* back side */
  .card-back {
    left: 560px;
    top: 90px;
    background: var(--navy);
    color: var(--paper);
  }
  .card-back .brand {
    position: absolute;
    left: 0; right: 0; top: 110px;
    display: flex; align-items: center; justify-content: center; gap: 18px;
  }
  .brand-dot {
    width: 34px; height: 34px; border-radius: 50%;
    border: 5px solid currentColor;
  }
  .brand-name {
    font-family: "Jost", sans-serif;
    font-weight: 600;
    font-size: 52px;
    letter-spacing: 4px;
  }
  .card-back .web {
    position: absolute;
    left: 0; right: 0; top: 240px;
    text-align: center;
    font-size: 20px;
    letter-spacing: 6px;
  }
  /* front side */
  .card-front {
    left: 40px;
    top: 520px;
    background: var(--paper);
  }
  .card-front .bands { position: absolute; inset: 0; }
  .card-front .brand {
    position: absolute;
    left: 30px; top: 120px;
    display: flex; align-items: center; gap: 12px;
    color: var(--navy);
  }
  .card-front .brand-name { font-size: 46px; letter-spacing: 3px; }
  .card-front .brand-dot { width: 26px; height: 26px; border-width: 4px; }
  .divider {
    position: absolute;
    left: 318px; top: 40px;
    width: 1px; height: 200px;
    background: var(--divider);
  }
  .contact {
    position: absolute;
    left: 345px; top: 48px;
    color: var(--ink);
  }
  .person-name { color: var(--navy); font-weight: 700; font-size: 28px; }
  .person-title { color: var(--teal); font-size: 19px; margin-bottom: 14px; }
  .line { display: flex; align-items: center; gap: 8px; font-size: 17px; line-height: 24px; }
  .line svg { width: 14px; height: 14px; flex: none; }
  .address { font-size: 17px; line-height: 21px; margin-top: 10px; }
  .card-front .web {
    position: absolute;
    right: 38px; top: 302px;
    color: var(--paper);
    font-size: 20px;
    letter-spacing: 6px;
  }
</style>
</head>
<body>
  <section class="card card-back">
    <div class="brand">
      <span class="brand-dot"></span>
      <span class="brand-name">VELUNDA</span>
    </div>
    <p class="web">www.velunda.com</p>
  </section>

  <section class="card card-front">
    <svg class="bands" width="600" height="340" viewBox="0 0 600 340">
      <polygon points="0,246 282,246 304,268 290,268 274,256 0,256" fill="var(--navy)"/>
      <polygon points="0,268 274,268 296,290 600,290 600,340 0,340" fill="var(--sky)"/>
    </svg>
    <div class="brand">
      <span class="brand-dot"></span>
      <span class="brand-name">VELUNDA</span>
    </div>
    <div class="divider"></div>
    <div class="contact">
      <p class="person-name">Your Name</p>
      <p class="person-title">Title</p>
      <p class="line">
        <svg viewBox="0 0 16 16"><circle cx="8" cy="8" r="7.5" fill="var(--navy)"/><path d="M5 4.5c0 4 2.5 6.8 6.5 7l.8-1.6-1.9-1-.9.9C8 9.2 6.9 8 6.5 6.6l.9-.9-1-1.9z" fill="#fff"/></svg>
        012-555-0147
      </p>
      <p class="line">
        <svg viewBox="0 0 16 16"><circle cx="8" cy="8" r="7.5" fill="var(--navy)"/><path d="M5 4.5c0 4 2.5 6.8 6.5 7l.8-1.6-1.9-1-.9.9C8 9.2 6.9 8 6.5 6.6l.9-.9-1-1.9z" fill="#fff"/></svg>
        012-555-0147
      </p>
      <p class="line">
        <svg viewBox="0 0 16 16"><rect x="1" y="3" width="14" height="10" rx="1" fill="var(--navy)"/><path d="M1.5 4l6.5 5 6.5-5" stroke="#fff" stroke-width="1.4" fill="none"/></svg>
        name@velunda.com
      </p>
      <p class="address">Street Name, City Name<br>State, City Zip Code</p>
    </div>
    <p class="web">www.velunda.com</p>
  </section>
</body>
</html>
```